Premium Food Label Design – High-End Boutique Jar Labels (3 Sizes)

I require a complete jar label redesign across three sizes:
75mm x 130mm (Large & Medium)
55mm x 120mm (Small)
45mm x 120mm (XS)

The design must feel professional, modern, elegant, and high-end boutique.
Primary aesthetic: white, minimal, refined, with accents in soft brown and gold/bronze. (see prefer colours of logo in OLD LABEL PDF)
Transparent background required.

I have attached my current label for wording reference only — I want to move away from the kraft look entirely.
The label must include all existing details, plus a dedicated space to manually add batch number and date.

IMPORTANT: Final files must be supplied as editable Adobe Illustrator (.AI) files with live text layers (not outlined) so I can update them as needed.
Logo is attached. I’m open to a fresh, elevated design direction aligned with a premium brand feel.

Target Market(s)

People who appreciate high-end, thoughtfully crafted food and are willing to pay for quality

Industry/Entity Type

Gourmet Food / Artisan Food Packaging

Requirements
Must have
• Premium, minimal aesthetic, Strong typography hierarchy, White background, Consistency across 3 sizes
Nice to have
• Elevated “Tide Lantern” styling
Should not have
• No bright or bold colours, No clutter or overcrowding, No heavy borders or thick frames,No “homemade/craft” fonts

```html
<!DOCTYPE html>
<html lang="en">
<head>
<meta charset="utf-8">
<title>Hearth Table – Tomato Relish Labels</title>
<link rel="stylesheet" href="https://fonts.googleapis.com/css2?family=Montserrat:wght@400;500;600;700;800;900&display=swap">
<style>
  :root {
    --canvas: #ececec;
    --label: #ffffff;
    --olive: #7b8043;
    --olive-deep: #6d7b2c;
    --cocoa: #4a3a2f;
    --taupe: #6a5b52;
    --relish: #9e2f17;
    --relish-dark: #6f1f10;
    --leaf: #5c7a2e;
    --bronze: #7a3d24;
    --grey: #8e8e8e;
    --grey-soft: #a5a5a5;
    --ink: #2f2f2f;
    --rule: #9a9a9a;
  }
  * { box-sizing: border-box; margin: 0; padding: 0; }
  html, body { width: 1200px; height: 4129px; overflow: hidden; }
  body { background: var(--canvas); font-family: "Montserrat", sans-serif; position: relative; }

  .label {
    position: absolute;
    background: var(--label);
    border-radius: 40px;
    box-shadow: 0 6px 24px rgba(0,0,0,0.06);
  }

  /* Front label */
  .label--front { left: 176px; top: 560px; width: 848px; height: 1000px; }

  .title-main, .title-sub {
    position: absolute;
    transform: rotate(-90deg);
    transform-origin: top left;
    white-space: nowrap;
  }
  .title-main {
    left: 37px; top: 936px;
    font-weight: 900; font-size: 196px; line-height: 144px;
    letter-spacing: -6px; color: var(--olive);
  }
  .title-sub {
    left: 205px; top: 942px;
    font-weight: 500; font-size: 66px; line-height: 67px;
    letter-spacing: 32px; color: var(--taupe);
  }
  .title-rule {
    position: absolute; left: 236px; top: 224px;
    width: 2px; height: 224px; background: #cfcfcf;
  }

  .brand-top {
    position: absolute; left: 330px; top: 44px; width: 240px;
    text-align: center; color: var(--cocoa);
    font-weight: 400; font-size: 40px; line-height: 48px; letter-spacing: 3px;
  }

  .hero-art {
    position: absolute; left: 293px; top: 128px; width: 555px; height: 768px;
    background:
      radial-gradient(ellipse 40% 10% at 58% 12%, #6f8f3a 0%, rgba(111,143,58,0) 100%),
      radial-gradient(ellipse 55% 45% at 45% 45%, var(--relish) 0%, var(--relish-dark) 70%, rgba(255,255,255,0) 100%);
    border-radius: 48% 48% 40% 40%;
  }

  .brand-small {
    position: absolute; left: 352px; top: 748px;
    color: #8a8a8a; font-weight: 700; font-size: 34px; line-height: 36px; letter-spacing: 1px;
  }
  .seal {
    position: absolute; left: 355px; top: 835px;
    width: 90px; height: 90px; border-radius: 50%;
    border: 3px solid #8fa14f; background: #f4f7ea;
  }
  .net-weight {
    position: absolute; left: 649px; top: 866px;
    font-weight: 900; font-size: 46px; color: var(--bronze); letter-spacing: -1px;
  }

  /* Back label */
  .label--back { left: 131px; top: 2620px; width: 938px; height: 1110px; }

  .intent-title {
    position: absolute; left: 0; top: 58px; width: 100%; text-align: center;
    font-weight: 800; font-size: 54px; color: var(--grey); letter-spacing: 0.5px;
  }
  .intent-text {
    position: absolute; left: 110px; top: 148px; width: 718px; text-align: center;
    font-weight: 500; font-size: 18.5px; line-height: 23px; color: var(--grey-soft);
  }
  .ingredients-title {
    position: absolute; left: 0; top: 256px; width: 100%; text-align: center;
    font-weight: 800; font-size: 40px; color: var(--olive-deep);
  }
  .ingredients {
    position: absolute; left: 152px; top: 316px; width: 634px;
    border-top: 2px dashed var(--rule); list-style: none;
  }
  .ingredients li {
    display: flex; justify-content: space-between; align-items: flex-end;
    height: 51px; padding-bottom: 2px;
    border-bottom: 2px solid #bdbdbd;
    font-weight: 500; font-size: 25px; color: var(--grey-soft);
  }
  .ingredients li:first-child { height: 59px; }

  .maker {
    position: absolute; left: 62px; top: 774px;
    font-weight: 600; font-size: 19.5px; line-height: 27px; color: var(--ink);
  }
  .storage {
    position: absolute; left: 493px; top: 804px;
    font-weight: 600; font-size: 19.5px; line-height: 27px; color: var(--ink);
  }
  .batch-box {
    position: absolute; left: 493px; top: 899px; width: 377px; height: 138px;
    border: 2px solid #9d9d9d; border-radius: 10px;
  }
  .batch-line {
    position: absolute; left: 62px; top: 952px;
    font-weight: 600; font-size: 17px; color: var(--ink);
  }
  .batch-line .blank {
    display: inline-block; border-bottom: 2px solid var(--ink); vertical-align: baseline;
  }
</style>
</head>
<body>

<section class="label label--front" aria-label="Front label">
  <div class="title-main">TOMATO</div>
  <div class="title-sub">RELISH</div>
  <div class="title-rule"></div>

  <div class="brand-top">HEARTH<br>TABLE</div>

  <div class="hero-art" role="img" aria-label="Heart-shaped window showing tomato relish with a green sprout on top"></div>

  <div class="brand-small">HEARTH<br><span style="font-size:20px;letter-spacing:3px;">TABLE</span></div>
  <div class="seal" aria-hidden="true"></div>

  <div class="net-weight">375G</div>
</section>

<section class="label label--back" aria-label="Back label">
  <h2 class="intent-title">TIDE LANTERN</h2>
  <p class="intent-text">WHAT IS MADE WITH LOVE IS FELT IN RETURN. MAY THIS RELISH NOURISH MORE THAN THE MEAL- BRINGING COMFORT, CONNECTION AND JOY TO EVERY MOMENT SHARED.</p>

  <h3 class="ingredients-title">INGREDIENT</h3>
  <ul class="ingredients">
    <li><span>TOMATO,</span><span>0GM</span></li>
    <li><span>ONION</span><span>0GM</span></li>
    <li><span>SUGAR,</span><span>0GM</span></li>
    <li><span>VINEGAR,</span><span>0GM</span></li>
    <li><span>SALT,</span><span>0GM</span></li>
    <li><span>SPICES,</span><span>0GM</span></li>
    <li><span>THIKENER ( CORNFLOWER)</span><span>0GM</span></li>
  </ul>

  <div class="maker">MADE BY HEARTH TABLE,QLD,<br>AUSTRALIA<br>W: HEARTHTABLE.COM<br>E: INFO@HEARTHTABLE.COM</div>
  <div class="storage">STORAGE:<br>KEEP REFRIGERATED<br>ONCE OPENED</div>

  <div class="batch-line">BATCH#<span class="blank" style="width:96px"></span>&nbsp; DATE <span class="blank" style="width:72px"></span></div>
  <div class="batch-box"></div>
</section>

</body>
</html>
```